High-end executive coaching group needs a 2 page digital flyer

We need a 2 page digital flyer for a high end leadership coaching offering for global leaders in healthcare. The flyer will advertise a new service (an elite senior leadership coaching group) for senior leaders in the healthcare industry from around the world.
The flyer should be upmarket, professional and minimalist in style to meet the expectations of my professional market (very senior doctors and executives).
The design should be based on my existing logo and brand, see my landing page: www.marlowadvisory.com
The key elements needed are
1) An editable PDF which we can update as we revise the specific details of the offering. The text and draft design for this is attached.
2) The banner image should be high quality but abstract. It can be based on the landing page of my website (the two ripple effects) but does not need to strictly adhere to this.
3) The logo placement of the Marlow Advisory delta sign should be discreet so that it does not dominate
4) The small logos of our professional accrediting organisations should be discreetly placed at the end and should not dominate. They might work best as mono icons in a footer (e.g. blue on a white background, or white on blue.
5) Please find enclosed a previous flyer as an example of a similar style we have used for more junior professionals. The design worked quite well, although we now need a more upmarket version for our senior executives.

Please note this design specifically needs to use existing branding and images from my website: marlowadvisory.com. We are definitely not looking for stock "leadership team" images for this high-end brochure.

Target Market(s)

Senior global leaders in the healthcare industry

Industry/Entity Type

Leading business schools & Healthcare industry.

Font styles to use
Other font styles liked:
• Operetta (selective use for heading) and Sofia Pro (body text)

Colors
0054AA
0677BA
7BADD7
CADEEF
E8F1F8

Requirements
Must have
• Clean minimalist and high professionally look that directly speaks to the interests and perspectives of senior leader leaders in healthcare. It also needs very clear call to action sections
Nice to have
• Effective presentation of the two bios and photographs. These need to look impressive, but should not dominate.
Should not have
• Loud and bold colours, large use of logos.

```html
<!DOCTYPE html>
<html lang="en">
<head>
<meta charset="utf-8">
<title>Marlow Advisory – Analytic Coaching Group for Senior Leaders</title>
<link href="https://fonts.googleapis.com/css2?family=Playfair+Display:wght@400;700;900&family=Mulish:wght@300;400;600;700&display=swap" rel="stylesheet">
<style>
:root{
  --navy:#22379a;
  --navy-deep:#1a2c82;
  --navy-ink:#1d2a6e;
  --blue-mid:#0054aa;
  --blue-soft:#7badd7;
  --blue-pale:#cadeef;
  --blue-wash:#e8f1f8;
  --paper:#ffffff;
  --paper-grey:#f5f6f9;
  --canvas:#e9eaee;
  --ink:#2b3150;
  --ink-soft:#545a74;
  --rule:#b9c0d8;
  --serif:"Playfair Display", Georgia, serif;
  --sans:"Mulish", "Helvetica Neue", Arial, sans-serif;
}
*{box-sizing:border-box;margin:0;padding:0}
html,body{width:1200px;height:3386px;overflow:hidden}
body{background:var(--canvas);font-family:var(--sans);color:var(--ink);position:relative}
.page{position:absolute;left:80px;width:1040px;height:1352px;background:var(--paper);overflow:hidden;box-shadow:0 6px 22px rgba(30,40,90,.12)}
.page--front{top:227px;background:var(--paper-grey)}
.page--back{top:1807px}
.abs{position:absolute}

/* ---------- front header ---------- */
.hero-art{position:absolute;left:390px;top:0;width:650px;height:408px;background:linear-gradient(160deg,#dfe6ea 0%,#b8c6cd 35%,#7f969f 58%,#c9d6da 78%,#8fb2b8 100%)}
.hero-white{position:absolute;left:0;top:0;width:1040px;height:181px;background:#fff}
.brand{position:absolute;left:118px;top:40px;font-family:var(--sans);font-weight:300;color:var(--navy);font-size:44px;line-height:44px}
.brand-dot{position:absolute;left:58px;top:60px;width:40px;height:40px;border-radius:50%;background:var(--navy)}
.hero-title{position:absolute;left:48px;top:205px;font-family:var(--serif);font-weight:900;color:#fff;font-size:58px;line-height:60px;letter-spacing:2px;text-transform:uppercase}

.subtitle{position:absolute;left:0;width:1040px;top:437px;text-align:center;font-weight:300;font-size:33px;color:var(--navy-ink)}
.pillars{position:absolute;left:88px;top:512px;display:flex;gap:38px;align-items:center}
.pillar{display:flex;align-items:center;gap:14px;font-size:22px;color:var(--ink);line-height:26px}
.pillar-icon{width:46px;height:46px;border-radius:7px;background:var(--navy);display:flex;align-items:center;justify-content:center}

.intro-photo{position:absolute;left:48px;top:620px;width:360px;height:172px;border:3px solid var(--blue-pale);background:linear-gradient(120deg,#f4f2ee 0%,#e6e9f0 45%,#cfd7e6 70%,#f1efeb 100%)}
.intro{position:absolute;left:452px;top:606px;width:560px}
.intro h2{font-weight:300;font-size:32px;line-height:34px;color:var(--navy-ink);margin-bottom:18px}
.intro p{font-size:12.5px;line-height:15px;color:var(--ink-soft);margin-bottom:8px}

.benefits{position:absolute;left:0;top:836px;width:1040px;height:262px;background:var(--navy)}
.benefits-tag{position:absolute;left:408px;top:820px;width:224px;height:36px;background:#fff;border:2px solid var(--navy);color:var(--navy);font-size:21px;text-align:center;line-height:32px;letter-spacing:.5px}
.benefit{position:absolute;display:flex;gap:16px;color:#fff;width:320px}
.benefit h3{font-family:var(--serif);font-weight:700;font-size:15px;line-height:17px;margin-bottom:4px}
.benefit p{font-size:12px;line-height:15px;color:#e2e7f5}
.benefit svg{flex:none}

.quote{position:absolute;left:48px;top:1118px;width:944px;font-size:12px;line-height:15px;color:var(--ink)}
.quote-text{width:620px;text-align:center}
.quote-mark{font-family:var(--serif);font-weight:900;font-size:26px;color:var(--navy);line-height:10px;vertical-align:-8px}
.quote-by{position:absolute;right:0;top:6px;font-size:18px;color:var(--ink)}
.quote-by::before{content:"";display:inline-block;width:36px;height:2px;background:var(--ink);vertical-align:middle;margin-right:14px}

.cta-left{position:absolute;left:48px;top:1194px;padding-left:18px;border-left:3px solid var(--navy);font-size:17px;line-height:21px;color:var(--navy-ink);text-transform:uppercase}
.details{position:absolute;left:312px;top:1198px;width:728px;height:124px;background:var(--navy);clip-path:polygon(80px 0,100% 0,100% 100%,0 100%)}
.details dl{position:absolute;color:#fff}
.details dt{font-family:var(--serif);font-weight:700;font-size:14px;letter-spacing:.5px;text-transform:uppercase}
.details dd{font-size:12.5px;line-height:15px}
.detail-row{position:absolute;display:flex;align-items:center;gap:14px;color:#fff}
.detail-row dt{font-family:var(--serif);font-weight:700;font-size:15px;width:58px;text-align:right}
.detail-row dd{font-size:12.5px;line-height:15px;border-left:1px solid #fff;padding-left:10px}
.small{font-size:10px}

/* ---------- back page ---------- */
.back-head{position:absolute;left:0;top:0;width:1040px;height:156px;background:var(--navy);color:#fff;text-align:center}
.back-head .kicker{position:absolute;top:48px;width:100%;font-family:var(--serif);font-size:25px}
.back-head h1{position:absolute;top:76px;width:100%;font-family:var(--serif);font-weight:900;font-size:44px;letter-spacing:2px;text-transform:uppercase}
.portrait{position:absolute;top:209px;width:403px;height:258px}
.portrait--left{left:49px;background:linear-gradient(160deg,#8fa67f 0%,#c8d3bd 30%,#d9c6b8 55%,#2e3f7a 85%)}
.portrait--right{left:593px;background:linear-gradient(160deg,#3a2a22 0%,#1e1614 40%,#b48a78 65%,#e6c9c4 100%)}
.bio{position:absolute;top:494px;width:403px}
.bio h2{font-family:var(--serif);font-weight:700;font-size:22px;text-align:center;color:var(--navy-ink);text-transform:uppercase;letter-spacing:.5px;line-height:24px}
.bio .role{text-align:center;font-size:14px;letter-spacing:4px;text-transform:uppercase;color:var(--ink-soft);margin-bottom:10px}
.bio p{font-size:14px;line-height:19.5px;color:var(--ink)}
.bio strong{font-family:var(--serif);font-weight:700}
.bio-divider{position:absolute;left:522px;top:548px;width:3px;height:214px;background:var(--navy)}

.explore{position:absolute;left:0;top:821px;width:1040px;height:262px;background:var(--navy);color:#fff}
.explore h2{position:absolute;left:49px;top:40px;padding-left:20px;border-left:3px solid #fff;font-weight:400;font-size:22px;line-height:28px;text-transform:uppercase;width:940px}
.explore ul{position:absolute;left:49px;top:124px;list-style:none;width:940px}
.explore li{font-size:17px;line-height:22px;padding:7px 0 7px 24px;border-bottom:1px solid rgba(255,255,255,.25);position:relative}
.explore li::before{content:"";position:absolute;left:2px;top:14px;border-left:8px solid #fff;border-top:5px solid transparent;border-bottom:5px solid transparent}
.explore li:last-child{border-bottom:none}

.spots{position:absolute;left:49px;top:1112px}
.spots h2{font-weight:400;font-size:23px;color:var(--navy-ink)}
.spots p{font-size:16px;line-height:20px;color:var(--ink)}
.back-quote{position:absolute;left:470px;top:1112px;width:525px;font-size:12px;line-height:15px;text-align:center}
.back-quote .by{position:absolute;right:0;top:66px;font-size:18px}
.back-quote .by::before{content:"";display:inline-block;width:36px;height:2px;background:var(--ink);vertical-align:middle;margin-right:14px}

.book{position:absolute;left:0;top:1207px;width:640px;height:120px;background:var(--navy);clip-path:polygon(0 0,590px 0,100% 100%,0 100%);color:#fff}
.book h2{position:absolute;left:0;width:590px;top:16px;text-align:center;font-family:var(--serif);font-weight:700;font-size:19px;letter-spacing:1px;text-transform:uppercase}
.book .line{position:absolute;left:49px;top:52px;width:540px;height:1px;background:rgba(255,255,255,.5)}
.contacts{position:absolute;left:49px;top:84px;font-size:12.5px;display:flex;gap:12px}
.contacts .ico{position:absolute;top:-20px;width:10px;height:8px;background:#fff;border-radius:1px}
.badges{position:absolute;left:645px;top:1224px;display:flex;align-items:center;gap:26px}
.badge{background:var(--blue-pale)}
</style>
</head>
<body>

<section class="page page--front">
  <div class="hero-white"></div>
  <div class="hero-art" role="img" aria-label="Abstract misty snow-capped mountain peak rising from still water"></div>
  <svg class="abs" style="left:0;top:0" width="1040" height="408" viewBox="0 0 1040 408" aria-hidden="true">
    <polygon points="0,0 560,0 390,181 0,181" fill="#fff"/>
    <polygon points="0,181 820,181 760,408 0,408" fill="var(--navy)"/>
    <polygon points="820,181 760,408 900,408" fill="var(--navy-deep)" opacity=".55"/>
    <polygon points="1010,0 1040,0 1040,60" fill="var(--navy)"/>
    <polygon points="1010,120 1040,90 1040,170" fill="var(--navy)" opacity=".7"/>
    <polygon points="1040,240 960,300 1040,360" fill="var(--navy)"/>
  </svg>
  <span class="brand-dot"></span>
  <div class="brand">Marlow<br>&nbsp;Advisory</div>
  <h1 class="hero-title">Elevate &amp;<br>Ignite Your<br>Leadership</h1>

  <p class="subtitle">Transformative Conversations for Senior Healthcare Leaders</p>

  <div class="pillars">
    <div class="pillar"><span class="pillar-icon"><svg width="22" height="26" viewBox="0 0 22 26"><path d="M5 11V7a6 6 0 0 1 12 0" stroke="#fff" stroke-width="3" fill="none"/><rect x="2" y="11" width="18" height="13" rx="2" fill="#fff"/></svg></span>Unlock Purpose</div>
    <div class="pillar"><span class="pillar-icon"><svg width="26" height="26" viewBox="0 0 26 26"><circle cx="13" cy="13" r="10" stroke="#fff" stroke-width="2.5" fill="none"/><circle cx="13" cy="13" r="4" fill="#fff"/></svg></span>Engage Authentically</div>
    <div class="pillar"><span class="pillar-icon"><svg width="24" height="28" viewBox="0 0 24 28"><rect x="3" y="3" width="18" height="22" rx="2" stroke="#fff" stroke-width="2.5" fill="none"/><path d="M8 17l4-6 4 6z" fill="#fff"/></svg></span>Amplify your<br>Leadership Impact</div>
  </div>

  <div class="intro-photo" role="img" aria-label="Photo of a small team discussing ideas at a whiteboard"></div>
  <div class="intro">
    <h2>Analytic Coaching Group for<br>Senior Leader</h2>
    <p>As a senior leader in healthcare, you’re constantly navigating challenges.<br>But where do you turn for authentic connections, reflection and personal growth?</p>
    <p>Rethink your leadership assumptions and approach challenges with fresh creativity.<br>Secure your spot in our exclusive Analytic Coaching Group and ignite your leadership potential.</p>
  </div>

  <div class="benefits"></div>
  <div class="benefits-tag">BENEFITS TO YOU</div>

  <div class="benefit" style="left:44px;top:878px">
    <svg width="86" height="70" viewBox="0 0 86 70"><circle cx="22" cy="30" r="9" fill="#fff"/><path d="M8 62c0-10 6-16 14-16s14 6 14 16z" fill="#fff"/><circle cx="60" cy="30" r="9" fill="#fff"/><path d="M46 62c0-10 6-16 14-16s14 6 14 16z" fill="#fff"/><path d="M30 8h24M48 3l6 5-6 5" stroke="#fff" stroke-width="2.5" fill="none"/></svg>
    <div><h3>Peer Insights</h3><p>Harness fresh insights from peers,<br>enhancing your decision-making<br>and effectiveness</p></div>
  </div>
  <div class="benefit" style="left:398px;top:870px">
    <svg width="70" height="70" viewBox="0 0 70 70"><rect x="26" y="4" width="36" height="22" rx="4" fill="#fff"/><circle cx="20" cy="40" r="8" fill="#fff"/><path d="M6 68c0-10 6-16 14-16s14 6 14 16z" fill="#fff"/><circle cx="48" cy="40" r="8" fill="#fff"/><path d="M34 68c0-10 6-16 14-16s14 6 14 16z" fill="#fff"/></svg>
    <div><h3>Transformative<br>Conversations</h3><p>Engage in discussions that<br>spark innovative leadership</p></div>
  </div>
  <div class="benefit" style="left:736px;top:872px">
    <svg width="76" height="66" viewBox="0 0 76 66"><path d="M38 2l4 8 9 1-7 6 2 9-8-5-8 5 2-9-7-6 9-1z" fill="#fff"/><circle cx="38" cy="36" r="7" fill="#fff"/><path d="M26 62c0-9 5-14 12-14s12 5 12 14z" fill="#fff"/><circle cx="14" cy="40" r="6" fill="#fff"/><path d="M3 64c0-8 4-12 11-12s11 4 11 12z" fill="#fff"/><circle cx="62" cy="40" r="6" fill="#fff"/><path d="M51 64c0-8 4-12 11-12s11 4 11 12z" fill="#fff"/></svg>
    <div><h3>Reimagined Leadership</h3><p>Channel your creativity and<br>redefine your leadership, personally<br>and professionally</p></div>
  </div>
  <div class="benefit" style="left:200px;top:980px">
    <svg width="76" height="60" viewBox="0 0 76 60"><rect x="4" y="12" width="54" height="40" rx="4" fill="#fff"/><path d="M14 26h30M14 36h22" stroke="var(--navy)" stroke-width="3"/><path d="M50 40l20-26 5 4-20 26-7 2z" fill="#fff" stroke="var(--navy)" stroke-width="2"/></svg>
    <div><h3>Instant 360 insights</h3><p>Gain real-time feedback<br>from trusted peers to enrich<br>your leadership</p></div>
  </div>
  <div class="benefit" style="left:538px;top:978px">
    <svg width="64" height="66" viewBox="0 0 64 66"><circle cx="32" cy="18" r="14" fill="#fff"/><path d="M30 10h4v10h-4zM27 14h10" stroke="var(--navy)" stroke-width="2"/><path d="M12 64c0-14 8-24 20-24s20 10 20 24z" fill="#fff"/><path d="M32 40v24" stroke="var(--navy)" stroke-width="2"/></svg>
    <div><h3>Lead authentically</h3><p>Develop effective strategies using<br>the latest insights from group and<br>leadership psychology</p></div>
  </div>

  <div class="quote">
    <p class="quote-text"><span class="quote-mark">“</span> You bare your heart &amp; share things you wouldn’t under normal circumstances. You get to know each other very quickly. There’s that sort of intense, shared experience that comes from speaking to each other’s lives. <span class="quote-mark">”</span></p>
    <span class="quote-by">Claire, Medical Director</span>
  </div>

  <p class="cta-left">Secure your spot now<br>and &nbsp;ignite your<br>leadership potential.</p>

  <div class="details">
    <dl class="detail-row" style="left:80px;top:24px"><dt>DATES</dt><dd>7 February – 11<br>December (2024)</dd></dl>
    <dl class="detail-row" style="left:80px;top:74px"><dt>TIME</dt><dd>7:30am – 8:45am<br>(UK time)</dd></dl>
    <dl style="left:310px;top:20px"><dt>Commitment :</dt><dd>Wednesdays, every 2 weeks</dd></dl>
    <svg class="abs" style="left:310px;top:60px" width="200" height="2"><line x1="0" y1="1" x2="200" y2="1" stroke="#fff" stroke-dasharray="2 3"/></svg>
    <dl style="left:310px;top:70px"><dt>Location :</dt><dd>Connect from anywhere by MeetLine</dd></dl>
    <dl style="left:560px;top:14px"><dt>Cost</dt><dd>£3350 [UK]<br>€3900 [Europe]<br>A$6530 [Australia]<br><span class="small">Payment options available</span></dd></dl>
  </div>
</section>

<section class="page page--back">
  <header class="back-head">
    <p class="kicker">Expertly guided by insight, academic rigour &amp; practical</p>
    <h1>Leadership Strategies</h1>
  </header>

  <svg class="abs" style="left:0;top:156px" width="1040" height="360" viewBox="0 0 1040 360" aria-hidden="true">
    <polygon points="0,150 49,120 49,200" fill="var(--blue-pale)"/>
    <polygon points="452,80 520,120 452,160" fill="var(--rule)"/>
    <polygon points="480,110 520,135 480,160" fill="var(--blue-soft)" opacity=".7"/>
    <polygon points="593,200 520,250 593,290" fill="var(--blue-pale)"/>
    <polygon points="535,120 560,90 560,150" fill="var(--navy)" opacity=".25"/>
    <polygon points="996,80 1040,60 1040,130" fill="var(--blue-pale)"/>
    <polygon points="996,160 1030,185 996,210" fill="var(--rule)"/>
  </svg>

  <div class="portrait portrait--left" role="img" aria-label="Portrait photo of Professor Daniel Hartley"></div>
  <div class="portrait portrait--right" role="img" aria-label="Portrait photo of Dr Helen Ashford"></div>

  <article class="bio" style="left:49px">
    <h2>Daniel Hartley</h2>
    <p class="role">Professor</p>
    <p><strong>Professor Daniel Hartley</strong> has 30 years’ experience developing leaders. An award-winning business school professor, group analyst and psychoanalytic psychotherapist, he has taught senior leadership programmes at the University of Northbridge, Kingsmead College London &amp; the University of Southport. His extensive leadership experience as a public health service clinical director and consultant psychotherapist inform his work as an accredited executive coach. With a PhD from Westbury College, University of Eastmoor, he is an expert in melding psychological insights with strategic organisational change.</p>
  </article>
  <div class="bio-divider"></div>
  <article class="bio" style="left:593px">
    <h2>Dr Helen Ashford</h2>
    <p class="role">Psychoanalyst</p>
    <p><strong>Dr Helen Ashford</strong> is a renowned psychoanalyst, group analyst, consultant psychiatrist and organisational consultant in the health sector. She has 20 years of leadership within the public health service, and she was also the National Director of Therapies for the Harbour Group, directing therapy services across 100 UK hospitals. She holds prominent positions as Chair of the Patient Safety Group, Chair of the Working Group on the Effect of Suicide and Homicide on Psychiatrists, and Vice Chair of the Psychotherapy Faculty at the Royal Society of Psychiatric Practice.</p>
  </article>

  <section class="explore">
    <h2>Engage with global leaders, gain diverse insights and forge lasting<br>bonds. Explore questions such as:</h2>
    <ul>
      <li>What kind of leader do I aspire to be in the next chapter of my life and career?</li>
      <li>What unique qualities and actions do I offer that no one else can?</li>
      <li>How can I galvanise my personal strengths to inspire and motivate others?</li>
    </ul>
  </section>

  <div class="spots">
    <h2>LIMITED SPOTS AVAILABLE</h2>
    <p>Don’t miss this unique opportunity to<br>transform your leadership journey.</p>
  </div>
  <div class="back-quote">
    <p><span class="quote-mark">“</span> Through this exceptional coaching, our leadership team elevated its performance to lead the hospital with greater clarity, cohesion and thoughtfulness. Not only do we provide a superior work environment for staff, but better care for our patients. <span class="quote-mark">”</span></p>
    <span class="by">Peter, CEO</span>
  </div>

  <div class="book">
    <h2>‹ Book your free discovery call ›</h2>
    <span class="line"></span>
    <div class="contacts">
      <span style="position:relative">daniel@marlowadvisory.com<i class="ico" style="left:80px"></i></span><span>|</span>
      <span style="position:relative">helenashford@mailbox.com<i class="ico" style="left:80px"></i></span><span>|</span>
      <span style="position:relative">www.marlowadvisory.com<i class="ico" style="left:75px;border-radius:50%"></i></span>
    </div>
  </div>

  <div class="badges" aria-label="Accrediting organisations">
    <span class="badge" style="width:54px;height:54px;border-radius:50%"></span>
    <span class="badge" style="width:70px;height:34px;border-radius:4px"></span>
    <span class="badge" style="width:70px;height:40px;border-radius:4px"></span>
    <span class="badge" style="width:90px;height:30px;border-radius:4px"></span>
  </div>
</section>

</body>
</html>
```